Plazabook Ads - Spiritual Project

We are looking for Plazabook - Ads for one of our spiritual projects. This project is about the holy grail and Jesus. Customers can buy this glass with the energy of the grail in it. With this they get some channels from the other side. These are real CD's in the customers. For the time being we wanna give them a really special offer, so they'll get the first one out of 12 for a very awesome priece. The customers get a free channeling on the website. They could hear it directly. With the grails they will become so many different kind of energy. With these energies they could work for customers, too. These energies are the highest at the planet for this time. So we need some illustrations, or otherwise nice banners for plazabook with a grail in it. The illustration could be the same by all 3 different adds. Here are some examples for the different kind of designs: 1. ) Jesus graphic in the background. Hands wants to give the grail to the customers. Text: Now become Guardian of the Holy Grail! Maybe with a christmas cap. Under the graphic: Your first Hlg. Grail at Christmas time. "And than 85 Euro crossed out and 40 Euro besides Down: www.lichtakademie-nord.de 2.) Angels in the middle of the holy grail. love, devotion In German language "Wonder, Love, Devotion." Under the graphic: Your first Holy Grail at Christmas ". And than 85 euros crossed out and 40 euros besides. Down: www.lichtakademie-nord.de 3.) The grail in the middle with a red cap on it. Same message like before. 4.) A crib and jesus is born situation and in the crib is the grail. Message is: The holy grail in you. In English: The Holy Grail in you! Than the priece and so on like before. You are free which technique you want. Illustration, Clouds and so on. Here you can find some information about the grails: https: //www.lichtakademie-nord. DE / kelchhüter / In this price psd files which we could work with are included. If you have any questions please feel free to contact me. Thank you! Torsten

Target Market(s)

Spiritual market

Number of Pages Required

3 page

Font styles to use
Sans Serif
Other font styles liked:
• look to the website which will happen

Colors
33a6d7
85cae6

Requirements
Must have
• It wants to work in the plazabook ads. We need it as jpg and psd, too. The logo of the Lumen Academy have to be in it. The Domain www.lichtakademie-nord.de have to be in it. An image of a grail to be in it. Nice design, logo, grail in it, message and price.
Nice to have
• It wants to be nice to make an emotional layout, maybe with some christmas ideas in it. Jesus could be in one of the designs, too. It wants to make 3 different kind of designs, so we can make A / B splits which of them performed.
Should not have
• Please dont bring a bible style in it. We need it for the new age scene.

```html
<!DOCTYPE html>
<html lang="de">
<head>
<meta charset="utf-8">
<title>Wächter der Heiligen Grale – Weihnachtsangebot</title>
<link rel="stylesheet" href="https://fonts.googleapis.com/css2?family=Baloo+2:wght@600;800&display=swap">
<style>
  :root {
    --sky-deep: #3f86cf;
    --sky-mid: #6fb0e6;
    --sky-light: #bfe2f8;
    --glow: #ffffff;
    --brand-blue: #33a6d7;
    --brand-pale: #85cae6;
    --ink-navy: #123a6b;
    --text-white: #ffffff;
  }
  * { box-sizing: border-box; margin: 0; padding: 0; }
  html, body { width: 1200px; height: 444px; overflow: hidden; background: var(--sky-deep); }
  .ad {
    position: relative;
    width: 1200px;
    height: 444px;
    overflow: hidden;
    font-family: "Baloo 2", sans-serif;
    background:
      radial-gradient(ellipse 260px 200px at 590px 90px, rgba(255,255,255,0.95), rgba(255,255,255,0) 70%),
      radial-gradient(ellipse 520px 330px at 590px 200px, rgba(191,226,248,0.9), rgba(191,226,248,0) 75%),
      linear-gradient(180deg, var(--sky-mid), var(--sky-deep));
  }
  .sky-clouds {
    position: absolute;
    inset: 0;
    background:
      radial-gradient(ellipse 200px 260px at 20px 120px, rgba(255,255,255,0.9), rgba(255,255,255,0) 70%),
      radial-gradient(ellipse 240px 150px at 120px 444px, rgba(255,255,255,0.85), rgba(255,255,255,0) 70%),
      radial-gradient(ellipse 210px 280px at 1190px 150px, rgba(255,255,255,0.9), rgba(255,255,255,0) 70%),
      radial-gradient(ellipse 260px 160px at 1080px 444px, rgba(255,255,255,0.85), rgba(255,255,255,0) 70%),
      radial-gradient(ellipse 420px 90px at 600px 444px, rgba(255,255,255,0.55), rgba(255,255,255,0) 70%);
  }
  .brand {
    position: absolute;
    top: 12px;
    left: 0;
    right: 0;
    display: flex;
    justify-content: center;
    align-items: center;
    gap: 8px;
  }
  .brand-dot {
    width: 36px;
    height: 36px;
    border-radius: 50%;
    background: var(--brand-blue);
  }
  .brand-name {
    font-weight: 800;
    font-size: 22px;
    color: var(--brand-blue);
    line-height: 1;
  }
  .headline {
    position: absolute;
    top: 62px;
    left: 0;
    right: 0;
    text-align: center;
    font-weight: 800;
    font-size: 29px;
    line-height: 1.12;
    color: var(--text-white);
    text-shadow:
      -2px -2px 0 var(--ink-navy), 2px -2px 0 var(--ink-navy),
      -2px 2px 0 var(--ink-navy), 2px 2px 0 var(--ink-navy),
      0 3px 4px rgba(18,58,107,0.5);
  }
  .grail-art {
    position: absolute;
    left: 460px;
    top: 138px;
    width: 265px;
    height: 212px;
    border-radius: 45% 45% 30% 30%;
    background: radial-gradient(ellipse at 50% 55%, #f4e2bf 0%, #d9b57c 30%, rgba(255,255,255,0.85) 55%, rgba(255,255,255,0) 75%);
  }
  .price-badge {
    position: absolute;
    left: 770px;
    top: 208px;
    width: 150px;
    height: 126px;
  }
  .price-badge svg { position: absolute; inset: 0; }
  .price-now, .price-was {
    position: absolute;
    left: 0;
    right: 0;
    text-align: center;
    font-weight: 800;
    color: var(--brand-blue);
    line-height: 1;
  }
  .price-now { top: 30px; font-size: 38px; }
  .price-was { top: 72px; font-size: 23px; text-decoration: line-through; text-decoration-thickness: 2px; }
  .offer-line {
    position: absolute;
    top: 362px;
    left: 0;
    right: 0;
    text-align: center;
    font-weight: 800;
    font-size: 22px;
    color: var(--text-white);
    text-shadow:
      -1.5px -1.5px 0 var(--ink-navy), 1.5px -1.5px 0 var(--ink-navy),
      -1.5px 1.5px 0 var(--ink-navy), 1.5px 1.5px 0 var(--ink-navy);
  }
  .site-url {
    position: absolute;
    top: 404px;
    left: 0;
    right: 0;
    text-align: center;
    font-weight: 600;
    font-size: 14px;
    color: var(--text-white);
    text-shadow: 0 1px 2px rgba(18,58,107,0.7);
  }
</style>
</head>
<body>
  <main class="ad">
    <div class="sky-clouds" role="img" aria-label="Heller Himmel mit Wolken an den Rändern und funkelnden Sternen"></div>

    <div class="brand">
      <span class="brand-dot"></span>
      <span class="brand-name">Lichtakademie Nord</span>
    </div>

    <h1 class="headline">Jetzt Wächter der<br>Heiligen Grale werden!</h1>

    <div class="grail-art" role="img" aria-label="Illustration: goldener Gralskelch mit weißen Flügeln, darüber eine segnende Figur im Licht"></div>

    <div class="price-badge">
      <svg viewBox="0 0 150 126" aria-hidden="true">
        <g fill="#ffffff" stroke="#33a6d7" stroke-width="4">
          <circle cx="40" cy="40" r="28"/>
          <circle cx="75" cy="28" r="28"/>
          <circle cx="110" cy="40" r="28"/>
          <circle cx="120" cy="78" r="28"/>
          <circle cx="92" cy="100" r="24"/>
          <circle cx="56" cy="100" r="24"/>
          <circle cx="30" cy="78" r="28"/>
        </g>
        <ellipse cx="75" cy="64" rx="62" ry="46" fill="#ffffff"/>
      </svg>
      <div class="price-now">€ 40</div>
      <div class="price-was">85</div>
    </div>

    <p class="offer-line">Dein erste Hlg. Gral zur Weihnachtszeit</p>
    <p class="site-url">www.lichtakademie-nord.de</p>
  </main>
</body>
</html>
```